BUSINESS CARD FOR GUITAR SCHOOL

I would like to design a business card for my Guitar Music School. The school is called "Pluck & Lantern".

The card should be yellow.

Target Market(s)

18-35 years old

Industry/Entity Type

School

Contact Information for Business Card

I would like to design a business card for my Guitar Music School. The school is called "Pluck & Lantern". The card should be yellow.

Card must be consistent with my website design: www.pluckandlantern.com.sg

Requirements
Must have
• 1) Name of Company
• 2) Company Logo
• 3) Name of Employee
• 4) Position of Employee
• 5) Contact Number
• 6) Address
Nice to have
• Creative Design
• Card must be consistent with my website design: www.pluckandlantern.com.sg
Should not have
• Boring Design

```html
<!DOCTYPE html>
<html lang="en">
<head>
<meta charset="utf-8">
<title>Pluck &amp; Lantern — Business Card</title>
<link rel="stylesheet" href="https://fonts.googleapis.com/css2?family=Open+Sans:wght@400;600;700;800&display=swap">
<style>
  :root {
    --backdrop: #e4e1dc;
    --card-yellow: #f7d600;
    --card-yellow-light: #fde83a;
    --card-yellow-deep: #f0c400;
    --ink: #1f2430;
    --card-shadow: rgba(60, 45, 20, 0.28);
  }
  * { box-sizing: border-box; margin: 0; padding: 0; }
  html, body {
    width: 1200px;
    height: 913px;
    overflow: hidden;
  }
  body {
    background: var(--backdrop);
    font-family: "Open Sans", Arial, sans-serif;
    color: var(--ink);
    display: flex;
    align-items: center;
    justify-content: center;
    gap: 48px;
  }
  .card {
    width: 530px;
    height: 303px;
    position: relative;
    border-radius: 3px;
    background: linear-gradient(160deg, var(--card-yellow-light) 0%, var(--card-yellow) 45%, var(--card-yellow-deep) 100%);
    box-shadow: 0 14px 30px var(--card-shadow);
  }

  /* Front */
  .card-front .wordmark {
    position: absolute;
    left: 60px;
    top: 108px;
  }
  .wordmark-name {
    font-weight: 800;
    font-size: 50px;
    line-height: 1;
    letter-spacing: -1.5px;
    color: var(--ink);
    white-space: nowrap;
  }
  .wordmark-tagline {
    font-weight: 600;
    font-size: 14px;
    margin-top: 8px;
    padding-left: 150px;
    color: var(--ink);
  }

  /* Back */
  .card-back .wordmark {
    position: absolute;
    right: 34px;
    top: 40px;
    text-align: right;
  }
  .card-back .wordmark-name {
    font-size: 30px;
    letter-spacing: -0.8px;
  }
  .card-back .wordmark-tagline {
    font-size: 9px;
    margin-top: 4px;
    padding-left: 0;
  }
  .holder {
    position: absolute;
    left: 36px;
    top: 128px;
  }
  .holder-name {
    font-weight: 700;
    font-size: 15px;
  }
  .holder-role {
    font-weight: 400;
    font-size: 11.5px;
    margin-top: 1px;
  }
  .address {
    position: absolute;
    left: 36px;
    top: 180px;
    font-size: 11.5px;
    line-height: 1.4;
  }
  .contact-list {
    position: absolute;
    left: 36px;
    top: 218px;
    list-style: none;
    font-size: 11.5px;
    line-height: 1.55;
  }
  .contact-list li {
    display: flex;
    align-items: center;
    gap: 8px;
  }
  .contact-list svg {
    width: 10px;
    height: 10px;
    fill: var(--ink);
    flex: none;
  }
  .contact-list .web { font-weight: 700; }
</style>
</head>
<body>

  <section class="card card-front" aria-label="Business card front">
    <div class="wordmark">
      <div class="wordmark-name">Pluck &amp; Lantern</div>
      <div class="wordmark-tagline">Taking Worship to the Next Level</div>
    </div>
  </section>

  <section class="card card-back" aria-label="Business card back">
    <div class="wordmark">
      <div class="wordmark-name">Pluck &amp; Lantern</div>
      <div class="wordmark-tagline">Taking Worship to the Next Level</div>
    </div>

    <div class="holder">
      <div class="holder-name">Your Long Name</div>
      <div class="holder-role">Managing Director</div>
    </div>

    <address class="address" style="font-style:normal">
      22 Keppel Lane Harbour Building<br>
      B #05-03 Singapore 418822
    </address>

    <ul class="contact-list">
      <li>
        <svg viewBox="0 0 10 10" aria-hidden="true"><path d="M1 3.2C1 2 2 1.5 5 1.5S9 2 9 3.2V4H7V3H3v1H1z M2.2 5h5.6L9 8.5H1z"/></svg>
        +65 91234567
      </li>
      <li>
        <svg viewBox="0 0 10 10" aria-hidden="true"><path d="M0.5 2h9v6h-9z M0.5 2l4.5 3.5L9.5 2" stroke="#fde83a" stroke-width="0.9"/></svg>
        yourname@pluckandlantern.com.sg
      </li>
      <li class="web">
        <svg viewBox="0 0 10 10" aria-hidden="true"><circle cx="5" cy="5" r="4.5"/></svg>
        www.pluckandlantern.com.sg
      </li>
    </ul>
  </section>

</body>
</html>
```